VORLAND COMPOSITES INC website in USA

VORLAND COMPOSITES INC incorporated and operated in USA needs a completely new design of website. This Wyoming based company is a importer and distributor of composites material to supply mainly to American and Canadian/Mexican customers. Our main products includes Carbon Fiber, Aramid Fiber, Glass Fiber, Basalt Fiber, High Silica Glass, Quartz Fiber, S-Glass, Alumina Fiber, Vacuum Auxiliary.

We are one stop composites solution provider for Automotive, Aerospace, Construction, Electrical and Machinery industries.

We are exclusive sales company in North America for BLORAN composites produced from China and their other Asia facilities.

Target Market(s)

USA and Canada

Industry/Entity Type

Composites materials

Coding

Coded - Design and coding required

Number of Pages Required

5+ page

Requirements
Nice to have
• Color theme to match our corporate logo VORLAND. VORLAND stands for Northgate Provisioning Trade Holdings

```html
<!DOCTYPE html>
<html lang="en">
<head>
<meta charset="utf-8">
<title>VORLAND Composites Inc.</title>
<link href="https://fonts.googleapis.com/css2?family=Montserrat:wght@400;500;600;800&display=swap" rel="stylesheet">
<style>
:root{
  --orange:#e99a26;
  --orange-soft:#fbe6c8;
  --cream:#fdf9f3;
  --dark:#2f2a27;
  --darker:#1f1c1a;
  --ink:#1c1c1c;
  --muted:#6b6b6b;
  --white:#ffffff;
}
*{box-sizing:border-box;margin:0;padding:0}
html,body{width:1200px;height:3408px;overflow:hidden}
body{font-family:'Montserrat',sans-serif;background:var(--cream);color:var(--ink)}
.page{position:relative;width:1200px;height:3408px;overflow:hidden}
.abs{position:absolute}

/* header */
.site-header{left:0;top:0;width:1200px;height:85px;background:var(--cream);display:flex;align-items:center;justify-content:space-between;padding:0 57px 0 58px;z-index:5}
.brand{display:flex;align-items:center;gap:12px;font-weight:800;font-size:30px;color:var(--orange);letter-spacing:1px}
.brand-dot{width:22px;height:22px;border-radius:50%;background:var(--orange)}
.main-nav{display:flex;align-items:center;gap:36px;font-size:15px;color:#555}
.main-nav .active{color:var(--orange);font-weight:600;text-decoration:underline;text-underline-offset:5px}
.btn{display:inline-flex;align-items:center;gap:10px;border-radius:22px;font-size:15px;font-weight:500;padding:5px 14px 5px 6px;color:var(--ink)}
.btn-orange{background:var(--orange)}
.btn-white{background:var(--white)}
.btn .ico{width:28px;height:28px;border-radius:50%;background:var(--white);display:flex;align-items:center;justify-content:center}
.btn-white .ico{background:var(--orange)}

/* hero */
.hero-photo{left:0;top:85px;width:1200px;height:620px;background:linear-gradient(160deg,#dcdcdc 0%,#a3a3a3 40%,#626262 70%,#3a3a3a 100%)}
.hero-panel{left:168px;top:229px;width:866px;height:291px;background:rgba(60,60,60,.62);border-radius:26px;text-align:center;color:var(--white);padding-top:24px}
.hero-title{font-size:44px;font-weight:800;color:var(--orange);line-height:1.1}
.hero-sub{font-size:44px;font-weight:500;line-height:1.15}
.hero-text{font-size:18px;line-height:1.45;margin:22px auto 22px;width:740px}

/* about */
.about-photo{left:145px;top:835px;width:390px;height:390px;border-radius:50%;background:radial-gradient(circle at 40% 45%,#4fb8de 0%,#2c7fa6 35%,#3a3a3a 70%,#b9b2a8 100%)}
.section-title{font-size:40px;font-weight:500}
.section-title b{color:var(--orange);font-weight:800}
.about-copy{left:612px;top:820px;width:475px}
.lead{font-size:16px;font-weight:500;line-height:1.55;margin:18px 0 20px}
.body-text{font-size:14.5px;line-height:1.72;color:var(--muted);text-align:justify;margin-bottom:12px}

/* products */
.products{left:0;top:1336px;width:1200px;height:609px;background:radial-gradient(ellipse at 50% 30%,#4a4440 0%,var(--dark) 60%,#292421 100%)}
.products .section-title{color:var(--white);text-align:center;padding-top:72px}
.card{top:175px;width:310px;height:346px;background:var(--white);border-radius:14px;overflow:hidden;text-align:center}
.card-img{height:232px}
.card h3{font-size:21px;font-weight:500;margin:22px 0 8px}
.card p{font-size:12.5px;color:var(--muted);line-height:1.45;padding:0 22px}
.arrow{top:325px;width:44px;height:44px;border-radius:50%;background:var(--white);display:flex;align-items:center;justify-content:center}

/* industries */
.industries{left:111px;top:2018px;width:980px}
.ind-lead{font-size:14px;line-height:1.75;margin:22px 0 36px;width:580px}
.ind-grid{display:grid;grid-template-columns:526px 450px;row-gap:38px}
.ind-item{display:flex;gap:24px}
.ind-icon{flex:none;width:68px;height:68px;border-radius:50%;background:var(--orange-soft);display:flex;align-items:center;justify-content:center}
.ind-icon span{width:34px;height:34px;border-radius:8px;background:var(--orange);opacity:.85}
.ind-item h4{font-size:21px;font-weight:500;margin-bottom:8px}
.ind-item p{font-size:13px;color:var(--muted);line-height:1.45;width:370px}
.divider{left:220px;top:2549px;width:770px;height:1px;background:#8a8a8a}
.divider-accent{left:470px;top:2546px;width:262px;height:7px;background:var(--orange)}

/* partnership */
.partner-logo{left:126px;top:2672px;width:390px;height:159px;background:var(--white);display:flex;align-items:center;justify-content:center;gap:18px;font-size:56px;font-weight:800;color:var(--darker);letter-spacing:3px}
.partner-logo i{width:40px;height:40px;background:var(--darker);display:block}
.partner-copy{left:612px;top:2632px;width:485px}

/* cta + footer */
.footer{left:0;top:3020px;width:1200px;height:388px}
.cta{left:140px;top:2954px;width:918px;height:171px;background:var(--orange);border-radius:30px;padding:40px 46px}
.cta h2{font-size:28px;font-weight:600;color:var(--darker)}
.cta p{font-size:14.5px;color:var(--white);line-height:1.6;margin-top:16px;width:480px;text-align:justify}
.cta .btn{position:absolute;right:48px;top:92px}
.footer-brand{left:0;top:3210px;width:1200px;justify-content:center;color:var(--white)}
.footer-nav{left:0;top:3315px;width:1200px;display:flex;justify-content:center;gap:44px;font-size:15px;color:var(--white)}
.footer-rule{left:112px;top:3351px;width:976px;height:1px;background:#6b6460}
.copyright{left:0;top:3368px;width:1200px;text-align:center;font-size:12.5px;color:var(--white)}
</style>
</head>
<body>
<div class="page">

  <header class="site-header abs">
    <div class="brand"><span class="brand-dot"></span>VORLAND</div>
    <nav class="main-nav">
      <span class="active">Home</span><span>About</span><span>Products</span><span>Industries</span><span>Resources</span>
      <span class="btn btn-orange"><span class="ico"><svg width="14" height="14" viewBox="0 0 24 24"><path fill="#2f2a27" d="M6.6 10.8a15 15 0 006.6 6.6l2.2-2.2a1 1 0 011-.25 11.4 11.4 0 003.6.57 1 1 0 011 1V20a1 1 0 01-1 1A17 17 0 013 4a1 1 0 011-1h3.5a1 1 0 011 1c0 1.25.2 2.45.57 3.57a1 1 0 01-.25 1z"/></svg></span>Contact Us</span>
    </nav>
  </header>

  <div class="hero-photo abs" role="img" aria-label="Photo: carbon fiber fabric sheet feeding through an industrial press"></div>

  <svg class="abs" style="left:0;top:560px" width="1200" height="800" viewBox="0 0 1200 800">
    <path d="M0 40 C180 100 420 140 600 150 C820 150 1040 90 1200 40 L1200 800 L0 800 Z" fill="#fdf9f3"/>
    <path d="M0 40 C180 100 420 140 600 150 L600 150 L512 160 L265 776 L0 776 Z" fill="#e99a26"/>
    <path d="M0 48 C160 100 380 140 594 150" stroke="#2f2a27" stroke-width="9" fill="none"/>
    <path d="M606 150 C820 145 1040 90 1200 44" stroke="#e99a26" stroke-width="9" fill="none"/>
  </svg>

  <section class="hero-panel abs">
    <h1 class="hero-title">Your One-Stop Composites Solution</h1>
    <p class="hero-sub">For North America</p>
    <p class="hero-text">Supplying advanced Carbon, Aramid, Glass, and Specialty Fibers for automotive, aerospace, construction, and industrial applications.</p>
    <span class="btn btn-orange"><span class="ico"><svg width="14" height="14" viewBox="0 0 24 24"><path fill="#2f2a27" d="M6.6 10.8a15 15 0 006.6 6.6l2.2-2.2a1 1 0 011-.25 11.4 11.4 0 003.6.57 1 1 0 011 1V20a1 1 0 01-1 1A17 17 0 013 4a1 1 0 011-1h3.5a1 1 0 011 1c0 1.25.2 2.45.57 3.57a1 1 0 01-.25 1z"/></svg></span>Explore Products</span>
  </section>

  <svg class="abs" style="left:110px;top:800px" width="460" height="460" viewBox="0 0 460 460">
    <circle cx="230" cy="230" r="227" fill="#fdf9f3" stroke="#1c1c1c" stroke-width="2"/>
    <circle cx="230" cy="230" r="212" fill="none" stroke="#e99a26" stroke-width="2"/>
  </svg>
  <div class="about-photo abs" role="img" aria-label="Photo: gloved hands rolling a carbon fiber tube"></div>

  <section class="about-copy abs">
    <h2 class="section-title"><b>About</b> Us</h2>
    <p class="lead">Supplying High-Performance Composite Materials Across the Americas</p>
    <p class="body-text">VORLAND Composites Inc., based in Wyoming, USA, is an importer and distributor of advanced composite materials, serving customers throughout the United States, Canada, and Mexico. We are the exclusive North American sales partner for BLORAN Composites, a globally recognized producer of high-quality composite fabrics and materials.</p>
    <p class="body-text" style="text-align:left">Sed ut perspiciatis unde omnis iste natus error sit voluptatem accusantium doloremque laudantium,</p>
    <span class="btn btn-orange" style="margin-top:6px"><span class="ico"><svg width="14" height="14" viewBox="0 0 24 24"><path fill="#2f2a27" d="M6.6 10.8a15 15 0 006.6 6.6l2.2-2.2a1 1 0 011-.25 11.4 11.4 0 003.6.57 1 1 0 011 1V20a1 1 0 01-1 1A17 17 0 013 4a1 1 0 011-1h3.5a1 1 0 011 1c0 1.25.2 2.45.57 3.57a1 1 0 01-.25 1z"/></svg></span>Read More</span>
  </section>

  <section class="products abs">
    <h2 class="section-title"><b>Our</b> Products</h2>
    <div class="arrow abs" style="left:41px"><svg width="16" height="16" viewBox="0 0 16 16"><path d="M10 2 4 8l6 6" stroke="#1c1c1c" stroke-width="2" fill="none"/></svg></div>
    <article class="card abs" style="left:111px">
      <div class="card-img" role="img" aria-label="Photo: gloved hands laying a carbon fiber sheet" style="background:linear-gradient(135deg,#6d6d6d,#2b2b2b)"></div>
      <h3>Carbon Fiber</h3>
      <p>Lorem ipsum dolor sit amet, consectetur adipiscing elit, sed do eiusmod</p>
    </article>
    <article class="card abs" style="left:445px">
      <div class="card-img" role="img" aria-label="Photo: close-up of woven aramid fiber" style="background:linear-gradient(135deg,#4f6a8a,#15202e)"></div>
      <h3>Aramid Fiber</h3>
      <p>Lorem ipsum dolor sit amet, consectetur adipiscing elit, sed do eiusmod</p>
    </article>
    <article class="card abs" style="left:778px">
      <div class="card-img" role="img" aria-label="Photo: rolled alumina fiber mesh" style="background:linear-gradient(135deg,#a86a55,#4a2419)"></div>
      <h3>Alumina Fiber</h3>
      <p>Lorem ipsum dolor sit amet, consectetur adipiscing elit, sed do eiusmod</p>
    </article>
    <div class="arrow abs" style="left:1115px"><svg width="16" height="16" viewBox="0 0 16 16"><path d="M6 2l6 6-6 6" stroke="#1c1c1c" stroke-width="2" fill="none"/></svg></div>
  </section>

  <section class="industries abs">
    <h2 class="section-title"><b>Industries</b> We Serve</h2>
    <p class="ind-lead">Lorem ipsum dolor sit amet, consectetur adipiscing elit, sed do eiusmod tempor incididunt ut labore et dolore magna aliqua</p>
    <div class="ind-grid">
      <div class="ind-item"><div class="ind-icon" role="img" aria-label="Automotive icon"><span></span></div><div><h4>Automotive</h4><p>Lorem ipsum dolor sit amet, consectetur adipiscing elit, sed do eiusmod</p></div></div>
      <div class="ind-item"><div class="ind-icon" role="img" aria-label="Aerospace icon"><span></span></div><div><h4>Aerospace</h4><p>Lorem ipsum dolor sit amet, consectetur adipiscing elit, sed do eiusmod</p></div></div>
      <div class="ind-item"><div class="ind-icon" role="img" aria-label="Construction icon"><span></span></div><div><h4>Construction</h4><p>Lorem ipsum dolor sit amet, consectetur adipiscing elit, sed do eiusmod</p></div></div>
      <div class="ind-item"><div class="ind-icon" role="img" aria-label="Electrical icon"><span></span></div><div><h4>Electrical</h4><p>Lorem ipsum dolor sit amet, consectetur adipiscing elit, sed do eiusmod</p></div></div>
      <div class="ind-item"><div class="ind-icon" role="img" aria-label="Machinery icon"><span></span></div><div><h4>Machinery</h4><p>Lorem ipsum dolor sit amet, consectetur adipiscing elit, sed do eiusmod</p></div></div>
    </div>
  </section>

  <div class="divider abs"></div>
  <div class="divider-accent abs"></div>

  <div class="partner-logo abs"><i></i>BLORAN</div>
  <section class="partner-copy abs">
    <h2 class="section-title"><b>Exclusive</b> Partnership</h2>
    <p class="lead" style="width:400px">Exclusive Distributor for BLORAN Composites in North America</p>
    <p class="body-text" style="text-align:left">Through our partnership with BLORAN Composites, VORLAND delivers world-class fiber technologies produced in China and across Asia ensuring consistent quality, technical excellence, and competitive pricing.</p>
  </section>

  <svg class="footer abs" width="1200" height="388" viewBox="0 0 1200 388">
    <path d="M0 70 C300 20 900 20 1200 70 L1200 388 L0 388 Z" fill="#1f1c1a"/>
    <path d="M0 86 L110 48" stroke="#2f2a27" stroke-width="8"/>
    <path d="M1090 38 L1200 70" stroke="#e99a26" stroke-width="8"/>
  </svg>

  <section class="cta abs">
    <h2>Ready to Source Premium Composite Materials?</h2>
    <p>Connect with our sales team for tailored solutions and fast logistics across North America.</p>
    <span class="btn btn-white"><span class="ico"><svg width="14" height="14" viewBox="0 0 24 24"><path fill="#2f2a27" d="M6.6 10.8a15 15 0 006.6 6.6l2.2-2.2a1 1 0 011-.25 11.4 11.4 0 003.6.57 1 1 0 011 1V20a1 1 0 01-1 1A17 17 0 013 4a1 1 0 011-1h3.5a1 1 0 011 1c0 1.25.2 2.45.57 3.57a1 1 0 01-.25 1z"/></svg></span>Contact Us</span>
  </section>

  <div class="brand footer-brand abs" style="display:flex;font-size:40px"><span class="brand-dot" style="width:28px;height:28px"></span>VORLAND</div>
  <nav class="footer-nav abs"><span>Home</span><span>About</span><span>Products</span><span>Industries</span><span>Resources</span><span>Contact Us</span></nav>
  <div class="footer-rule abs"></div>
  <p class="copyright abs">Copyright © 2025 Vorland. All rights reserved.</p>

</div>
</body>
</html>
```